Vantrel Activated Carbon (coal-based)

The packaging for granular activated carbon must have a simple industrial concept but looks classy. Industrial look, bold and credible, also eye catching. Weight: 25 kg

Target Market(s)

Industrial

Industry/Entity Type

Water Treatment Industry

Requirements
Must have
• Weight : 25 kg, must have "coal-based", warning symbol in packaging
Nice to have
• There is a picture of granular activated carbon (coal-based) on the package

```html
<!DOCTYPE html>
<html lang="en">
<head>
<meta charset="utf-8">
<title>Vantrel Activated Carbon – Packaging</title>
<link href="https://fonts.googleapis.com/css2?family=Montserrat:wght@600;800;900&family=Roboto:wght@400;500;700&display=swap" rel="stylesheet">
<style>
  :root{
    --bg:#4a6b9c;
    --bag:#0b0b0d;
    --blue:#2a6ec1;
    --blue-light:#4f8fd8;
    --white:#ffffff;
    --grey:#5d5f64;
    --text-muted:#c8ccd3;
  }
  *{box-sizing:border-box;margin:0;padding:0}
  html,body{width:699px;height:1200px;overflow:hidden}
  body{background:var(--bg);font-family:"Roboto",sans-serif;color:var(--white);position:relative}

  /* front panel */
  .front-panel{position:absolute;left:185px;top:50px;width:330px;height:470px;background:var(--bag);overflow:hidden}
  .halftone{position:absolute;border-radius:50%}
  .front-panel .halftone.top{right:-90px;top:-60px;width:260px;height:260px;background:radial-gradient(circle,rgba(42,110,193,.55) 0%,rgba(42,110,193,.15) 55%,transparent 70%)}
  .front-panel .halftone.bottom{left:-80px;bottom:-110px;width:300px;height:300px;background:radial-gradient(circle,rgba(42,110,193,.6) 0%,rgba(42,110,193,.15) 55%,transparent 70%)}
  .brand-mark{position:absolute;left:18px;top:28px;display:flex;flex-direction:column;align-items:center;gap:3px}
  .brand-mark .dot{width:14px;height:14px;border:2px solid var(--white);border-radius:50%}
  .brand-mark span{font-family:"Montserrat",sans-serif;font-weight:600;font-size:6px;letter-spacing:.5px}
  .title-block{position:absolute;left:22px;top:125px;right:22px}
  .coal-based{font-family:"Montserrat",sans-serif;font-weight:600;font-size:8px;letter-spacing:1px;text-align:right;padding-right:54px;color:var(--text-muted)}
  .product-name{font-family:"Montserrat",sans-serif;font-weight:900;font-size:46px;letter-spacing:1px;line-height:1;color:var(--white)}
  .product-type{display:flex;align-items:center;gap:6px;margin-top:6px;font-family:"Montserrat",sans-serif;font-weight:800;font-size:12px;letter-spacing:.5px}
  .product-type .premium{background:var(--blue);padding:3px 6px}
  .languages{margin-top:8px;font-size:9px;line-height:1.6;color:var(--text-muted)}
  .info-bar{margin-top:10px;background:var(--grey);padding:5px 8px;font-size:6px;line-height:1.4;color:var(--text-muted)}
  .weight-badge{position:absolute;right:22px;bottom:70px;width:44px;height:44px;border-radius:50%;background:var(--white);color:var(--bag);font-family:"Montserrat",sans-serif;font-weight:800;font-size:13px;display:flex;align-items:center;justify-content:center}

  /* dieline */
  .dieline{position:absolute;left:82px;top:600px;width:536px;height:558px;background:var(--bag);overflow:hidden}
  .panel{position:absolute;top:0;height:100%}
  .flap-line{position:absolute;left:0;right:0;height:1px;background:#222}
  .side-strip{position:absolute;top:100px;bottom:100px;background:var(--blue);display:flex;align-items:center;justify-content:center}
  .side-strip span{writing-mode:vertical-rl;transform:rotate(180deg);font-family:"Montserrat",sans-serif;font-weight:800;font-size:10px;letter-spacing:1px}
  .mini-title{font-family:"Montserrat",sans-serif;font-weight:900;letter-spacing:.5px;line-height:1}
  .mini-type{display:flex;gap:4px;align-items:center;font-family:"Montserrat",sans-serif;font-weight:800;margin-top:4px}
  .mini-type .premium{background:var(--blue);padding:2px 4px}
  .warning{display:flex;gap:5px;font-size:6px;line-height:1.5;color:var(--text-muted);margin-top:10px}
  .icons{display:flex;gap:6px;margin-top:10px}
  .icons span{width:12px;height:12px;border:1px solid var(--text-muted);border-radius:2px}
  .white-box{width:34px;height:14px;background:var(--white);margin-top:14px}
</style>
</head>
<body>

<section class="front-panel" aria-label="Front of bag">
  <div class="halftone top" role="img" aria-label="Blue halftone dot pattern"></div>
  <div class="halftone bottom" role="img" aria-label="Blue halftone dot pattern"></div>
  <div class="brand-mark"><i class="dot"></i><span>VANTREL</span></div>
  <div class="title-block">
    <p class="coal-based">COAL-BASED</p>
    <h1 class="product-name">VANTREL</h1>
    <p class="product-type"><span class="premium">PREMIUM</span><span>ACTIVATED CARBON</span></p>
    <p class="languages">活性炭 | Активированный уголь | كربون منشط<br>Charbon actif | Geactiveerde koolstof</p>
    <p class="info-bar">Granular activated carbon for industrial water treatment<br>and purification use</p>
  </div>
  <div class="weight-badge">25kg</div>
</section>

<section class="dieline" aria-label="Flat bag layout">
  <div class="flap-line" style="top:100px"></div>
  <div class="flap-line" style="bottom:100px"></div>

  <div class="panel back" style="left:0;width:190px;padding:115px 14px 0">
    <p class="mini-title" style="font-size:22px">VANTREL</p>
    <p class="mini-type" style="font-size:7px"><span class="premium">PREMIUM</span><span>ACTIVATED CARBON</span></p>
    <div class="warning">
      <svg width="16" height="14" viewBox="0 0 16 14" aria-label="Warning"><path d="M8 1 15 13H1Z" fill="none" stroke="#fff" stroke-width="1.3"/><path d="M8 5v4M8 10.5v1" stroke="#fff" stroke-width="1.3"/></svg>
      <p>Warning: keep dry, store sealed, avoid dust inhalation. Use protective gloves and mask when handling.</p>
    </div>
    <div class="icons"><span></span><span></span><span></span><span></span><span></span></div>
    <div class="white-box"></div>
  </div>

  <div class="side-strip" style="left:212px;width:26px"><span>PREMIUM ACTIVATED CARBON</span></div>

  <div class="panel front" style="left:258px;width:200px;padding:150px 14px 0">
    <div class="halftone" role="img" aria-label="Blue halftone dot pattern" style="left:-40px;bottom:60px;width:200px;height:200px;background:radial-gradient(circle,rgba(42,110,193,.55) 0%,transparent 70%)"></div>
    <p style="font-family:Montserrat,sans-serif;font-size:6px;text-align:right;color:var(--text-muted)">COAL-BASED</p>
    <p class="mini-title" style="font-size:28px">VANTREL</p>
    <p class="mini-type" style="font-size:8px"><span class="premium">PREMIUM</span><span>ACTIVATED CARBON</span></p>
    <p style="font-size:6px;color:var(--text-muted);margin-top:6px;line-height:1.6">活性炭 | Активированный уголь | كربون منشط<br>Charbon actif | Geactiveerde koolstof</p>
  </div>

  <div class="side-strip" style="left:476px;width:26px"><span>PREMIUM ACTIVATED CARBON</span></div>
</section>

</body>
</html>
```